Harborview Estates Business Card for Apartment Buildings

Create business cards for resident managers who run apartment buildings. The audience is the public who are searching for apartment rentals, and current residents who live at the apartment building. Key design element will be incorporating the company logo, however, the logo cannot dominate. The building name and manager name are more important than the logo. Current business card design leaves little room for copy, so we may need to reduce the size on the current card to allow for more space for copy.

Target Market(s)

Adults 18-65 years of age, who are looking for an apartment rental, plus current residents who live at our apartment buildings.

Industry/Entity Type

Property Management

Contact Information for Business Card

A major design element will be use of the company logo. Important property and manager contact information must be part of the design. The size of the logo will need to be reduced to make room for building and manager contact copy.

Font styles to use
Sans Serif

Colors
3176b5
000000
959595
ffffff

Requirements
Must have
• 1) Incorporate the company logo.
• 2) Use the company colors (dark blue, black/grey, over white).
• 3) FEATURE THE BUILDING NAME
• 4) FEATURE THE MANAGER NAME
• 5) The company name is less important than BUILDING and MANAGER
• 6) Manager contact information
• **SEE ATTACHED CREATIVE BRIEF**
Nice to have
• 1) Back of card logo watermark
• 2) Ability to write notes on back of carfd
Should not have
• Avoid letting the company logo dominate the card, the building name and manager are more important than the company logo.

```html
<!DOCTYPE html>
<html lang="en">
<head>
<meta charset="utf-8">
<title>Harborview Estates – Resident Manager Business Card</title>
<link rel="stylesheet" href="https://fonts.googleapis.com/css2?family=Arimo:wght@400;700&display=swap">
<style>
  :root {
    --brand-blue: #0e6aa8;
    --ink: #333333;
    --grey: #959595;
    --paper: #ffffff;
    --stage: #e6e7e9;
    --card-edge: #cfd0d2;
    --watermark: #f3f3f3;
  }
  * { margin: 0; padding: 0; box-sizing: border-box; }
  html, body { width: 1200px; height: 1200px; overflow: hidden; }
  body {
    background: var(--stage);
    font-family: "Arimo", Arial, sans-serif;
    color: var(--ink);
    position: relative;
  }
  .card {
    position: absolute;
    left: 257px;
    width: 686px;
    height: 392px;
    background: var(--paper);
    border: 1px solid var(--card-edge);
    overflow: hidden;
  }
  .card--front { top: 182px; }
  .card--back { top: 645px; }

  .company-name {
    position: absolute;
    display: flex;
    align-items: center;
    gap: 8px;
    color: var(--brand-blue);
    font-weight: 700;
    white-space: nowrap;
  }
  .company-name__dot {
    width: 14px; height: 14px; border-radius: 50%;
    background: var(--brand-blue);
    flex: none;
  }
  .card--front .company-name { left: 30px; top: 58px; font-size: 27px; }

  .manager { position: absolute; left: 389px; top: 74px; }
  .manager__name { color: var(--brand-blue); font-size: 28px; line-height: 1.2; }
  .manager__title { font-size: 13.5px; margin-top: 2px; }

  .property { position: absolute; left: 31px; top: 180px; }
  .property__name { color: var(--brand-blue); font-size: 18.5px; line-height: 1.2; margin-bottom: 2px; }
  .property__line { font-size: 15.5px; line-height: 1.2; }

  .contact { position: absolute; top: 257px; font-size: 14.5px; line-height: 18.5px; }
  .contact--left { left: 31px; }
  .contact--right { left: 210px; }
  .contact__row { display: flex; align-items: center; gap: 8px; }
  .contact__icon { width: 13px; height: 13px; flex: none; fill: var(--brand-blue); }

  .band { position: absolute; left: 0; top: 330px; width: 686px; height: 40px; }
  .band__url {
    position: absolute; left: 0; top: 340px; width: 546px;
    text-align: center;
    color: var(--paper); font-size: 13.5px; letter-spacing: 2.6px;
  }

  .watermark { position: absolute; left: 0; top: 0; }
  .card--back .company-name { right: 36px; top: 292px; font-size: 22px; }
  .back-url {
    position: absolute; right: 36px; top: 348px;
    font-size: 15px; letter-spacing: 0.6px; color: var(--ink);
  }
  .back-url strong { color: var(--brand-blue); font-weight: 400; }
</style>
</head>
<body>

<section class="card card--front" aria-label="Business card front">
  <div class="company-name"><span class="company-name__dot"></span>HARBORVIEW ESTATES</div>

  <div class="manager">
    <p class="manager__name">Marisol Delgado</p>
    <p class="manager__title">Resident Manager</p>
  </div>

  <div class="property">
    <p class="property__name">Cedar Court Apartments</p>
    <p class="property__line">2845 Linden Street</p>
    <p class="property__line">San Diego, CA 92116</p>
  </div>

  <div class="contact contact--left">
    <p class="contact__row">
      <svg class="contact__icon" viewBox="0 0 16 16" aria-hidden="true"><path d="M1 6c0-2 3-4 7-4s7 2 7 4v1h-3V5.5C11 5 9.5 4.8 8 4.8S5 5 4 5.5V7H1z"/><path d="M3 8l2-2h6l2 2v6H3z"/></svg>
      619-555-0142
    </p>
    <p class="contact__row">
      <svg class="contact__icon" viewBox="0 0 16 16" aria-hidden="true"><path d="M4 1h8v14H4zM5.5 2.5v10h5v-10z"/></svg>
      619-555-0187
    </p>
  </div>

  <div class="contact contact--right">
    <p class="contact__row">
      <svg class="contact__icon" viewBox="0 0 16 16" aria-hidden="true"><path d="M5 1h5l2 2v3H5z"/><path d="M1 7h14v7H1z"/></svg>
      619-555-0163
    </p>
    <p class="contact__row">
      <svg class="contact__icon" viewBox="0 0 16 16" aria-hidden="true"><path d="M1 3h14v10H1z"/><path d="M1.5 3.5L8 9l6.5-5.5" fill="none" stroke="#fff" stroke-width="1.4"/></svg>
      marisol@harborviewest.com
    </p>
  </div>

  <svg class="band" viewBox="0 330 686 40" width="686" height="40" aria-hidden="true">
    <polygon points="0,330 540,330 636,366 0,366" fill="var(--brand-blue)"/>
    <circle cx="520" cy="348" r="20" fill="var(--paper)"/>
    <circle cx="520" cy="348" r="14" fill="var(--brand-blue)"/>
  </svg>
  <p class="band__url">www.harborviewest.com</p>
</section>

<section class="card card--back" aria-label="Business card back">
  <svg class="watermark" width="686" height="392" viewBox="0 0 686 392" aria-hidden="true">
    <circle cx="206" cy="214" r="194" fill="var(--watermark)"/>
  </svg>
  <div class="company-name"><span class="company-name__dot"></span>HARBORVIEW ESTATES</div>
  <p class="back-url">www.<strong>harborviewest</strong>.com</p>
</section>

</body>
</html>
```